Stage Design Company Business Card

We are looking to step up up our business card design for our team.

We are a Full service Design and Consultation company for Stage and TV with an emphasis in Theatrical Lighting.

We like our materials to be clean and modern with solid colors free of patterns and gradients. Our brand consists of 4 primary colors Purple, Black, Grey, and White. Provided is our Word Mark as well as our Symbol Logo.

We would like our cards to leave an impression beyond the information, show our attention to design and detail, and make our marks an easily recognized feature (together or apart) for our clients.

We need a warm approachable comfortable feel for some clients, and a professional flair for the board member type clients.

Attached are our brand elements, and our existing cards to give a sense of our style and a glipse at the information we provide on our cards.

Target Market(s)

broad client base from church leaders to high school teachers and architects.

Industry/Entity Type

Business

Contact Information for Business Card

We format our phone number with periods not parenthesis or dashes. Information will be edited for each of our team members, and team member specific cards are not part of this scope, but rather a template so to speak.

Font styles to use
Sans Serif

Colors
6b449b
ffffff
000000
333333
aaaaaa

Requirements
Must have
• Wordmark and logo mark present (does not need to exist on the same side of card)
• Brand Colors,
• Name, Phone, Email, Address.
• Unique choices that make someone stop and take a second look
Nice to have
• It would be nice to somehow convey what we DO, as our brand name does not lend itself to this, outside of an obvious tagline though.....
• social media if not crowded. all of our handles match (instagram, twitter, facebook)
Should not have
• "clipart"

```html
<!DOCTYPE html>
<html lang="en">
<head>
<meta charset="utf-8">
<title>Kestrel Stage Business Card</title>
<link href="https://fonts.googleapis.com/css2?family=Jost:wght@400;500;700&display=swap" rel="stylesheet">
<style>
  :root {
    --brand-purple: #6b449b;
    --card-black: #111111;
    --backdrop: #2a2a2a;
    --ink-white: #ffffff;
    --ink-grey: #aaaaaa;
  }
  * { margin: 0; padding: 0; box-sizing: border-box; }
  html, body {
    width: 1200px; height: 900px; overflow: hidden;
    background: var(--backdrop);
    font-family: "Jost", "Futura", sans-serif;
  }
  .canvas {
    position: relative; width: 1200px; height: 900px;
  }
  .card {
    position: absolute; left: 290px; width: 620px; height: 354px;
    background: var(--card-black);
    border-radius: 4px;
    box-shadow: 0 12px 30px rgba(0,0,0,0.45);
  }
  .card-front { top: 70px; }
  .card-back { top: 470px; }

  /* Front */
  .front-brand {
    position: absolute; inset: 0;
    display: flex; flex-direction: column; align-items: center; justify-content: center; gap: 22px;
  }
  .brand-dot {
    width: 86px; height: 86px; border-radius: 50%;
    background: var(--ink-white);
  }
  .brand-name {
    color: var(--ink-white); font-weight: 500;
    font-size: 30px; letter-spacing: 0.35em; padding-left: 0.35em;
  }

  /* Back */
  .back-brand {
    position: absolute; left: 0; top: 0; width: 300px; height: 100%;
    display: flex; flex-direction: column; align-items: center; justify-content: center; gap: 20px;
  }
  .back-brand .brand-dot { width: 70px; height: 70px; background: var(--brand-purple); }
  .back-brand .brand-name { font-size: 22px; }
  .divider {
    position: absolute; left: 318px; top: 64px; width: 3px; height: 226px;
    background: var(--brand-purple);
  }
  .contact {
    position: absolute; left: 350px; top: 66px; color: var(--ink-white);
  }
  .person-name {
    color: var(--brand-purple); font-weight: 700; font-size: 30px; letter-spacing: 0.03em; line-height: 1;
  }
  .person-role { font-size: 21px; margin-top: 4px; }
  .address { font-size: 19px; line-height: 1.12; margin-top: 14px; letter-spacing: 0.04em; }
  .contact-list { list-style: none; margin-top: 14px; }
  .contact-list li {
    display: flex; align-items: center; gap: 14px;
    font-size: 19px; letter-spacing: 0.04em; line-height: 1.35;
  }
  .contact-list svg { width: 16px; height: 16px; flex: none; }
</style>
</head>
<body>
<main class="canvas">
  <section class="card card-front" aria-label="Card front">
    <div class="front-brand">
      <span class="brand-dot"></span>
      <span class="brand-name">KESTREL STAGE</span>
    </div>
  </section>

  <section class="card card-back" aria-label="Card back">
    <div class="back-brand">
      <span class="brand-dot"></span>
      <span class="brand-name">KESTREL STAGE</span>
    </div>
    <div class="divider"></div>
    <div class="contact">
      <p class="person-name">MARCUS T REEVE</p>
      <p class="person-role">Owner</p>
      <p class="address">214 N. Alder Ave<br>Tempe, AZ 85281</p>
      <ul class="contact-list">
        <li>
          <svg viewBox="0 0 16 16" aria-hidden="true"><rect x="4" y="1" width="8" height="14" rx="1.5" fill="none" stroke="#6b449b" stroke-width="1.6"/><line x1="7" y1="12.5" x2="9" y2="12.5" stroke="#6b449b" stroke-width="1.4"/></svg>
          800.555.0142
        </li>
        <li>
          <svg viewBox="0 0 16 16" aria-hidden="true"><rect x="1" y="3" width="14" height="10" fill="#6b449b"/><polyline points="1,3 8,9 15,3" fill="none" stroke="#111" stroke-width="1.4"/></svg>
          hello@kestrel-stage.com
        </li>
        <li>
          <svg viewBox="0 0 16 16" aria-hidden="true"><circle cx="6.5" cy="6.5" r="4.5" fill="none" stroke="#6b449b" stroke-width="2"/><line x1="10" y1="10" x2="15" y2="15" stroke="#6b449b" stroke-width="2.2"/></svg>
          kestrel-stage.com
        </li>
      </ul>
    </div>
  </section>
</main>
</body>
</html>
```